Quorva - corporate Business Card

We need a good look and innovative business card for a new start up company based in Los Angeles called "Quorva". We are in a payment business, including payment card, app, and ewallet. We are expert in online payment and Card not present (CNP) transaction.
We need an innovative, modern business card.

Our logo font is Aero Matics

Target Market(s)

Startup - Bank - Online Payment - Card Manufacturing

Industry/Entity Type

Startup

Contact Information for Business Card

phone: 555 014 7396 - Address: 4172 Marlowe blvd, Brenholt Park, CA 90299

Requirements
Must have
• Message: innovative, professional, expert, high tech, trust, online payment expert, security
Nice to have
• no comment
Should not have
• no Comment

```html
<!DOCTYPE html>
<html lang="en">
<head>
<meta charset="utf-8">
<title>Quorva – Business Card</title>
<link href="https://fonts.googleapis.com/css2?family=Open+Sans:wght@400;600&display=swap" rel="stylesheet">
<style>
  :root {
    --brand-red: #b81f2f;
    --card-white: #ffffff;
    --text-grey: #4a4a4a;
    --backdrop: #6e4c35;
    --shadow: rgba(0, 0, 0, 0.35);
  }
  * { margin: 0; padding: 0; box-sizing: border-box; }
  html, body {
    width: 1200px;
    height: 987px;
    overflow: hidden;
    background: var(--backdrop);
    font-family: "Open Sans", Arial, sans-serif;
  }
  .stage { position: relative; width: 1200px; height: 987px; }

  .card {
    position: absolute;
    left: 293px;
    width: 615px;
    height: 350px;
    box-shadow: 0 3px 8px var(--shadow);
  }
  .card--front { top: 130px; background: var(--card-white); }
  .card--back  { top: 506px; background: var(--brand-red); }

  /* Front */
  .brand {
    position: absolute;
    left: 45px;
    top: 48px;
    display: flex;
    align-items: center;
    gap: 12px;
  }
  .brand__dot {
    width: 74px;
    height: 74px;
    border-radius: 50%;
    background: var(--brand-red);
  }
  .brand__name {
    font-size: 50px;
    font-weight: 600;
    color: var(--brand-red);
    line-height: 1;
    letter-spacing: 0.5px;
  }

  .holder {
    position: absolute;
    right: 43px;
    top: 60px;
    text-align: right;
  }
  .holder__name {
    font-size: 21px;
    font-weight: 600;
    color: var(--brand-red);
    line-height: 26px;
  }
  .holder__title {
    font-size: 16px;
    color: var(--text-grey);
    line-height: 22px;
  }
  .edge-tab {
    position: absolute;
    right: 0;
    top: 61px;
    width: 14px;
    height: 45px;
    background: var(--brand-red);
  }

  .contacts {
    position: absolute;
    left: 47px;
    top: 243px;
    list-style: none;
  }
  .contacts__item {
    display: flex;
    align-items: center;
    gap: 9px;
    font-size: 16px;
    color: var(--text-grey);
    line-height: 23.5px;
  }
  .contacts__icon { width: 15px; height: 15px; fill: var(--brand-red); flex: none; }

  .address {
    position: absolute;
    right: 43px;
    top: 266px;
    text-align: right;
    font-size: 16px;
    font-style: normal;
    color: var(--text-grey);
    line-height: 23.5px;
  }

  /* Back */
  .emblem {
    position: absolute;
    left: 213px;
    top: 70px;
    width: 188px;
    height: 188px;
    border-radius: 50%;
    background: var(--card-white);
    display: flex;
    align-items: center;
    justify-content: center;
  }
  .emblem__name {
    font-size: 40px;
    font-weight: 600;
    color: var(--brand-red);
  }
  .back-url {
    position: absolute;
    left: 0;
    right: 0;
    top: 290px;
    text-align: center;
    font-size: 15px;
    color: var(--card-white);
    letter-spacing: 0.32em;
  }
</style>
</head>
<body>
<main class="stage">
  <section class="card card--front">
    <div class="brand">
      <span class="brand__dot"></span>
      <span class="brand__name">quorva</span>
    </div>

    <div class="holder">
      <p class="holder__name">DANIEL HARLOW</p>
      <p class="holder__title">CEO&amp;Founder</p>
    </div>
    <span class="edge-tab"></span>

    <ul class="contacts">
      <li class="contacts__item">
        <svg class="contacts__icon" viewBox="0 0 16 16" aria-hidden="true"><path d="M3.2 1.2l2.4 2.6-1.2 1.8c.9 2 2.5 3.6 4.4 4.6l1.8-1.2 2.6 2.4-1.6 2.4C6.4 13.4 2 9 1 3z"/></svg>
        555 014 7396
      </li>
      <li class="contacts__item">
        <svg class="contacts__icon" viewBox="0 0 16 16" aria-hidden="true"><path d="M1 3.5h14v9H1z"/><path d="M2 4.5l6 4.5 6-4.5" stroke="#fff" stroke-width="1.2" fill="none"/></svg>
        daniel@quorva.com
      </li>
      <li class="contacts__item">
        <svg class="contacts__icon" viewBox="0 0 16 16" aria-hidden="true"><circle cx="8" cy="8" r="7"/><path d="M1 8h14M8 1c-3 3-3 11 0 14M8 1c3 3 3 11 0 14" stroke="#fff" stroke-width="1" fill="none"/></svg>
        www.quorva.com
      </li>
    </ul>

    <address class="address">
      4172 Marlowe blvd<br>
      Brenholt Park, CA 90299
    </address>
  </section>

  <section class="card card--back">
    <div class="emblem">
      <span class="emblem__name">quorva</span>
    </div>
    <p class="back-url">www.quorva.com</p>
  </section>
</main>
</body>
</html>
```